Stage Design Company Business Card

We are looking to step up up our business card design for our team.

We are a Full service Design and Consultation company for Stage and TV with an emphasis in Theatrical Lighting.

We like our materials to be clean and modern with solid colors free of patterns and gradients. Our brand consists of 4 primary colors Purple, Black, Grey, and White. Provided is our Word Mark as well as our Symbol Logo.

We would like our cards to leave an impression beyond the information, show our attention to design and detail, and make our marks an easily recognized feature (together or apart) for our clients.

We need a warm approachable comfortable feel for some clients, and a professional flair for the board member type clients.

Attached are our brand elements, and our existing cards to give a sense of our style and a glipse at the information we provide on our cards.

Target Market(s)

broad client base from church leaders to high school teachers and architects.

Industry/Entity Type

Business

Contact Information for Business Card

We format our phone number with periods not parenthesis or dashes. Information will be edited for each of our team members, and team member specific cards are not part of this scope, but rather a template so to speak.

Font styles to use
Sans Serif

Colors
6b449b
ffffff
000000
333333
aaaaaa

Requirements
Must have
• Wordmark and logo mark present (does not need to exist on the same side of card)
• Brand Colors,
• Name, Phone, Email, Address.
• Unique choices that make someone stop and take a second look
Nice to have
• It would be nice to somehow convey what we DO, as our brand name does not lend itself to this, outside of an obvious tagline though.....
• social media if not crowded. all of our handles match (instagram, twitter, facebook)
Should not have
• "clipart"

```html
<!DOCTYPE html>
<html lang="en">
<head>
<meta charset="utf-8">
<title>Lumen Business Card</title>
<link href="https://fonts.googleapis.com/css2?family=Open+Sans:wght@400;600;700&display=swap" rel="stylesheet">
<style>
  :root {
    --backdrop: #3a3532;
    --card: #0c0c0c;
    --ink: #d9d9d9;
    --ink-soft: #aaaaaa;
    --accent: #6b449b;
  }
  * { margin: 0; padding: 0; box-sizing: border-box; }
  html, body {
    width: 1200px;
    height: 900px;
    overflow: hidden;
    background: var(--backdrop);
    font-family: "Open Sans", sans-serif;
  }
  .stage {
    position: relative;
    width: 1200px;
    height: 900px;
  }
  .card {
    position: absolute;
    top: 301px;
    width: 520px;
    height: 297px;
    background: var(--card);
    box-shadow: 0 12px 30px rgba(0,0,0,0.45);
  }
  .card--front { left: 60px; }
  .card--back { left: 620px; }

  .brand {
    position: absolute;
    left: 0;
    top: 0;
    width: 215px;
    height: 297px;
    display: flex;
    align-items: center;
    justify-content: center;
    gap: 10px;
  }
  .brand__dot {
    width: 12px;
    height: 12px;
    border-radius: 50%;
    background: var(--accent);
  }
  .brand__name {
    font-size: 24px;
    font-weight: 600;
    letter-spacing: 9px;
    color: var(--ink);
  }
  .divider {
    position: absolute;
    left: 215px;
    top: 72px;
    width: 1px;
    height: 150px;
    background: var(--accent);
  }
  .details {
    position: absolute;
    left: 232px;
    top: 70px;
    color: var(--ink);
  }
  .details__name {
    font-size: 15px;
    font-weight: 700;
    letter-spacing: 0.5px;
    text-transform: uppercase;
    line-height: 1.1;
  }
  .details__title {
    font-size: 11px;
    color: var(--ink-soft);
    margin-bottom: 16px;
  }
  .contact {
    list-style: none;
    font-size: 11.5px;
    line-height: 18px;
  }
  .contact li {
    display: flex;
    align-items: center;
    gap: 8px;
  }
  .contact svg {
    width: 9px;
    height: 9px;
    fill: var(--accent);
    flex: none;
  }
  .address {
    margin-top: 12px;
    font-size: 11.5px;
    line-height: 17px;
  }

  .card--back .brand {
    width: 520px;
  }
  .card--back .brand__name {
    font-size: 34px;
    letter-spacing: 14px;
  }
  .card--back .brand__dot {
    width: 16px;
    height: 16px;
  }
</style>
</head>
<body>
<main class="stage">
  <section class="card card--front" aria-label="Business card front">
    <div class="brand">
      <span class="brand__dot"></span>
      <span class="brand__name">LUMEN</span>
    </div>
    <div class="divider"></div>
    <div class="details">
      <p class="details__name">Marcus Hale</p>
      <p class="details__title">Managing Director</p>
      <ul class="contact">
        <li>
          <svg viewBox="0 0 10 10" aria-hidden="true"><path d="M2 0.5 L3.6 2.6 L2.7 3.7 Q3.8 5.9 6.2 7.3 L7.3 6.4 L9.5 8 L8.4 9.5 Q2 8.5 0.5 1.6 Z"/></svg>
          <span>044.555.019.284</span>
        </li>
        <li>
          <svg viewBox="0 0 10 10" aria-hidden="true"><path d="M0.5 2 H9.5 V8 H0.5 Z M1 2.4 L5 5.4 L9 2.4" fill="none" stroke="#6b449b" stroke-width="1"/><path d="M0.5 2 H9.5 L5 5.3 Z"/></svg>
          <span>info@lumenstage.com</span>
        </li>
        <li>
          <svg viewBox="0 0 10 10" aria-hidden="true"><circle cx="5" cy="5" r="4.5"/></svg>
          <span>www.lumenstage.com</span>
        </li>
      </ul>
      <p class="address">1234, Address GoesHere,<br>Country name, 12345</p>
    </div>
  </section>

  <section class="card card--back" aria-label="Business card back">
    <div class="brand">
      <span class="brand__dot"></span>
      <span class="brand__name">LUMEN</span>
    </div>
  </section>
</main>
</body>
</html>
```